Dog grooming business card
This is a business card for m dog grooming business like it say above.
In the priorities box below I will have the text that I want on the card.

Industry/Entity Type

Business

Colors

Designer to choose colors to be used in the design.

Requirements
Must have
• My logo and the insurance stamp must be on the card.

Text it must have :

Professional grooming services
Email: lunabrisk@mailvale.net
Text or call 1 705 318 6052
TWF certified/member
Pet first aid certified
Next appointment ___________________________________
Nice to have
• Greens to match my logo

```html
<!DOCTYPE html>
<html lang="en">
<head>
<meta charset="utf-8">
<title>Luna Brisk – Business Card</title>
<link rel="stylesheet" href="https://fonts.googleapis.com/css2?family=Arimo:wght@400&family=Lobster&display=swap">
<style>
  :root {
    --canvas: #e6e2dc;
    --paper: #ffffff;
    --ink: #231f20;
    --leaf: #96c13b;
    --leaf-text: #8dbf2e;
    --badge-edge: #2f8fd6;
    --shadow: rgba(0,0,0,0.18);
  }
  * { margin: 0; padding: 0; box-sizing: border-box; }
  html, body { width: 1200px; height: 870px; overflow: hidden; }
  body {
    background: var(--canvas);
    font-family: "Arimo", Arial, sans-serif;
    position: relative;
  }
  .card {
    position: absolute;
    top: 138px;
    width: 340px;
    height: 594px;
    background: var(--paper);
    box-shadow: 0 6px 18px var(--shadow);
    overflow: hidden;
  }
  .card--back { left: 220px; }
  .card--front { left: 640px; }

  /* Back side */
  .appointment {
    position: absolute;
    left: 0; right: 0;
    top: 232px;
    text-align: center;
  }
  .appointment__title {
    color: var(--leaf-text);
    font-size: 19px;
    letter-spacing: 0.5px;
    margin-bottom: 10px;
  }
  .appointment__line {
    width: 270px;
    margin: 0 auto 22px;
    border-top: 3px dotted var(--ink);
  }
  .contact {
    font-size: 17px;
    color: var(--ink);
    line-height: 1.55;
  }
  .contact__label { color: var(--leaf-text); }

  /* Front side */
  .front-art { position: absolute; inset: 0; }
  .brand {
    position: absolute;
    top: 100px; left: 0; right: 0;
    display: flex;
    flex-direction: column;
    align-items: center;
    gap: 16px;
  }
  .brand__dot {
    width: 70px; height: 70px;
    border-radius: 50%;
    background: var(--leaf);
  }
  .brand__name {
    font-family: "Arimo", Arial, sans-serif;
    font-weight: 400;
    font-size: 36px;
    letter-spacing: 0.5px;
    color: var(--leaf);
  }
  .tagline {
    position: absolute;
    top: 352px; left: 0; right: 0;
    text-align: center;
    font-family: "Lobster", cursive;
    font-size: 25px;
    color: var(--ink);
  }
  .credentials {
    position: absolute;
    top: 412px; left: 0; right: 0;
    text-align: center;
    font-size: 17px;
    line-height: 1.45;
    color: var(--ink);
  }
  .insurance-badge {
    position: absolute;
    top: 482px;
    left: 50%;
    transform: translateX(-50%);
    width: 86px; height: 38px;
    border-radius: 8px;
    background: var(--paper);
    border: 2px solid var(--badge-edge);
  }
</style>
</head>
<body>

  <section class="card card--back" aria-label="Card back">
    <div class="appointment">
      <p class="appointment__title">NEXT APPOINTMENT</p>
      <div class="appointment__line"></div>
      <div class="appointment__line"></div>
      <p class="contact"><span class="contact__label">Email</span> lunabrisk@mailvale.net</p>
      <p class="contact"><span class="contact__label">Text</span> or <span class="contact__label">Call</span> 1 705 318 6052</p>
    </div>
  </section>

  <section class="card card--front" aria-label="Card front">
    <svg class="front-art" viewBox="0 0 340 594" preserveAspectRatio="none" aria-hidden="true">
      <rect width="340" height="594" fill="var(--leaf)"/>
      <path d="M0 0 H340 V318 Q170 318 0 262 Z" fill="var(--paper)"/>
      <path d="M0 0 H340 V302 Q170 302 0 248 Z" fill="var(--ink)"/>
    </svg>

    <div class="brand">
      <span class="brand__dot"></span>
      <span class="brand__name">Luna Brisk</span>
    </div>

    <p class="tagline">Professional grooming services</p>
    <div class="credentials">
      <p>TWF certified/member</p>
      <p>Pet first aid certified</p>
    </div>
    <div class="insurance-badge" role="img" aria-label="Insurance stamp"></div>
  </section>

</body>
</html>
```